Quorva - corporate Business Card

We need a good look and innovative business card for a new start up company based in Los Angeles called "Quorva". We are in a payment business, including payment card, app, and ewallet. We are expert in online payment and Card not present (CNP) transaction.
We need an innovative, modern business card.

Our logo font is Aero Matics

Target Market(s)

Startup - Bank - Online Payment - Card Manufacturing

Industry/Entity Type

Startup

Contact Information for Business Card

phone: 555 014 7396 - Address: 4172 Marlowe blvd, Cylver City, CA 90299

Requirements
Must have
• Message: innovative, professional, expert, high tech, trust, online payment expert, security
Nice to have
• no comment
Should not have
• no Comment

```html
<!DOCTYPE html>
<html lang="en">
<head>
<meta charset="utf-8">
<title>Quorva — Business Card</title>
<link rel="stylesheet" href="https://fonts.googleapis.com/css2?family=Open+Sans:wght@400;600;700&display=swap">
<style>
  :root {
    --brand-red: #b81e32;
    --paper-white: #ffffff;
    --ink-grey: #6b6b6b;
    --backdrop: #2b2b2d;
  }
  * { margin: 0; padding: 0; box-sizing: border-box; }
  html, body {
    width: 1200px; height: 950px; overflow: hidden;
    background: var(--backdrop);
    font-family: "Open Sans", Arial, sans-serif;
  }
  .sheet {
    width: 1200px; height: 950px;
    display: flex; flex-direction: column; align-items: center; justify-content: center;
    gap: 50px;
  }
  .card {
    position: relative;
    width: 700px; height: 400px;
    overflow: hidden;
  }

  /* Front */
  .card-front { background: var(--paper-white); }
  .name-tab {
    position: absolute; top: 40px; right: 0;
    width: 250px; height: 90px;
    background: var(--brand-red);
    color: var(--paper-white);
    padding: 18px 28px 0 20px;
    text-align: right;
    white-space: nowrap;
  }
  .name-tab .person { font-size: 21px; font-weight: 700; line-height: 1.2; }
  .name-tab .role { font-size: 16px; font-weight: 400; line-height: 1.3; }

  .brand-lockup {
    position: absolute; left: 50px; top: 120px;
    display: flex; align-items: center; gap: 14px;
  }
  .brand-dot {
    width: 74px; height: 74px; border-radius: 50%;
    background: var(--brand-red);
    flex: none;
  }
  .brand-name {
    color: var(--brand-red);
    font-size: 64px; font-weight: 600; line-height: 1;
    letter-spacing: -1px;
  }

  .contact {
    position: absolute; left: 70px; top: 235px;
    color: var(--ink-grey); font-size: 16px; line-height: 1.45;
  }
  .contact .address { margin-bottom: 10px; }
  .contact-line { display: flex; align-items: center; gap: 10px; }
  .contact-line svg { width: 16px; height: 16px; flex: none; }

  /* Back */
  .card-back { background: var(--brand-red); }
  .back-lockup {
    position: absolute; left: 0; right: 0; top: 120px;
    display: flex; align-items: center; justify-content: center; gap: 20px;
  }
  .back-lockup .brand-dot { width: 120px; height: 120px; background: var(--paper-white); }
  .back-lockup .brand-name { color: var(--paper-white); font-size: 96px; }
  .back-web {
    position: absolute; left: 0; right: 0; bottom: 60px;
    text-align: center;
    color: var(--paper-white);
    font-size: 14px; letter-spacing: 8px;
  }
</style>
</head>
<body>
<main class="sheet">

  <section class="card card-front" aria-label="Business card front">
    <div class="name-tab">
      <div class="person">Dana Whitlock</div>
      <div class="role">President</div>
    </div>

    <div class="brand-lockup">
      <span class="brand-dot"></span>
      <span class="brand-name">Quorva</span>
    </div>

    <div class="contact">
      <p class="address">4172 Marlowe blvd<br>Brenmoor Heights, CA 90299</p>
      <p class="contact-line">
        <svg viewBox="0 0 16 16" aria-hidden="true"><path fill="#b81e32" d="M3 1h3l1.5 3.5-2 1.3a8 8 0 0 0 4.7 4.7l1.3-2L15 10v3a2 2 0 0 1-2 2A12 12 0 0 1 1 3a2 2 0 0 1 2-2z"/></svg>
        555 014 7396
      </p>
      <p class="contact-line">
        <svg viewBox="0 0 16 16" aria-hidden="true"><rect x="1" y="3" width="14" height="10" rx="1" fill="#b81e32"/><path d="M1.5 4l6.5 5 6.5-5" stroke="#fff" stroke-width="1.3" fill="none"/></svg>
        dana@quorva.com
      </p>
      <p class="contact-line">
        <svg viewBox="0 0 16 16" aria-hidden="true"><circle cx="8" cy="8" r="7" fill="#b81e32"/><path d="M1 8h14M8 1c3 3 3 11 0 14M8 1c-3 3-3 11 0 14" stroke="#fff" stroke-width="1" fill="none"/></svg>
        www.quorva.com
      </p>
    </div>
  </section>

  <section class="card card-back" aria-label="Business card back">
    <div class="back-lockup">
      <span class="brand-dot"></span>
      <span class="brand-name">Quorva</span>
    </div>
    <p class="back-web">www.quorva.com</p>
  </section>

</main>
</body>
</html>
```